Business Management Fortress

Assist with enhancing a powerpoint slide by providing a few design options for consideration. I have a template but open to any creative ideas.

Internal employees and stakeholders

Business Management, Finance, Accounting

• Maintain a fortress, temple, or pyramid schema
• Scenic Background

```html
<!DOCTYPE html>
<html lang="en">
<head>
<meta charset="utf-8">
<title>Business Management Fortress</title>
<link rel="stylesheet" href="https://fonts.googleapis.com/css2?family=Outfit:wght@400;500&display=swap">
<style>
  :root {
    --sky-top: #1c2e52;
    --mountain: #2a4270;
    --lake: #3a5aa0;
    --forest: #0c1a2a;
    --line: #ffffff;
    --panel: rgba(8, 16, 38, 0.55);
    --panel-soft: rgba(8, 16, 38, 0.35);
    --ink-dark: #0d1428;
  }
  html, body {
    margin: 0;
    padding: 0;
    width: 1200px;
    height: 683px;
    overflow: hidden;
    background: var(--forest);
  }
  .slide {
    position: relative;
    width: 1200px;
    height: 683px;
    overflow: hidden;
    font-family: "Outfit", sans-serif;
  }
  .scenery {
    position: absolute;
    inset: 0;
    background:
      radial-gradient(ellipse 55% 30% at 50% 42%, rgba(120,150,220,0.45), transparent 70%),
      radial-gradient(ellipse 30% 60% at 6% 45%, rgba(8,22,26,0.9), transparent 70%),
      radial-gradient(ellipse 30% 60% at 94% 45%, rgba(8,22,26,0.9), transparent 70%),
      linear-gradient(180deg, var(--sky-top) 0%, var(--mountain) 28%, var(--lake) 48%, #2c4680 70%, var(--forest) 100%);
  }
  .temple {
    position: absolute;
    inset: 0;
  }
  .frame {
    fill: var(--panel);
    stroke: var(--line);
    stroke-width: 2;
  }
  .frame-soft { fill: var(--panel-soft); }
  .roof-label {
    fill: var(--line);
    font-weight: 500;
    text-anchor: middle;
    letter-spacing: 0.5px;
  }
  .pillar-label {
    fill: var(--line);
    font-weight: 500;
    text-anchor: middle;
    letter-spacing: 0.5px;
  }
  .tab { fill: var(--line); }
  .tab-label {
    fill: var(--ink-dark);
    font-size: 12.5px;
    font-weight: 500;
    text-anchor: middle;
    letter-spacing: 0.3px;
  }
  .duty-line {
    fill: var(--line);
    font-size: 13px;
    font-weight: 500;
    text-anchor: middle;
    letter-spacing: 0.2px;
  }
</style>
</head>
<body>
<main class="slide">
  <div class="scenery" role="img" aria-label="Mountain lake at dusk framed by pine forest, with peaks reflected in still blue water"></div>

  <svg class="temple" width="1200" height="683" viewBox="0 0 1200 683" xmlns="http://www.w3.org/2000/svg">
    <!-- roof -->
    <g class="roof">
      <polygon class="frame" points="225,170 225,144 399,93 591,170"/>
      <polygon class="frame" points="613,170 804,93 975,144 975,170"/>
      <polygon class="frame" points="411,90 600,34 789,90 600,166"/>
      <text class="roof-label" x="600" y="103" font-size="28">PARTNER</text>
      <text class="roof-label" x="399" y="154" font-size="22">LEADER</text>
      <text class="roof-label" x="816" y="154" font-size="22">PROFITABILITY</text>
    </g>

    <!-- entablature -->
    <rect class="frame frame-soft" x="269" y="178" width="670" height="36"/>

    <!-- pillars -->
    <g class="pillar">
      <rect class="frame" x="271" y="222" width="112" height="18"/>
      <rect class="frame" x="286" y="246" width="82" height="11"/>
      <rect class="frame" x="303" y="264" width="48" height="11"/>
      <rect class="frame" x="303.5" y="285" width="47" height="156"/>
      <rect class="frame" x="303" y="447" width="48" height="11"/>
      <rect class="frame" x="286" y="464" width="82" height="12"/>
      <rect class="frame" x="273" y="482" width="109" height="18"/>
      <text class="pillar-label" font-size="20" transform="translate(334,363) rotate(-90)">PEOPLE</text>
    </g>
    <g class="pillar">
      <rect class="frame" x="461" y="222" width="112" height="18"/>
      <rect class="frame" x="476" y="246" width="82" height="11"/>
      <rect class="frame" x="493" y="264" width="48" height="11"/>
      <rect class="frame" x="493.5" y="285" width="47" height="156"/>
      <rect class="frame" x="493" y="447" width="48" height="11"/>
      <rect class="frame" x="476" y="464" width="82" height="12"/>
      <rect class="frame" x="462" y="482" width="110" height="18"/>
      <text class="pillar-label" font-size="20" transform="translate(524,363) rotate(-90)">INNOVATION</text>
    </g>
    <g class="pillar">
      <rect class="frame" x="648" y="222" width="112" height="18"/>
      <rect class="frame" x="663" y="246" width="82" height="11"/>
      <rect class="frame" x="680" y="264" width="48" height="11"/>
      <rect class="frame" x="680.5" y="285" width="47" height="156"/>
      <rect class="frame" x="680" y="447" width="48" height="11"/>
      <rect class="frame" x="663" y="464" width="82" height="12"/>
      <rect class="frame" x="649" y="482" width="110" height="18"/>
      <text class="pillar-label" font-size="18" transform="translate(703,363) rotate(-90)">BUSINESS</text>
      <text class="pillar-label" font-size="18" transform="translate(721,363) rotate(-90)">INTELLIGENCE</text>
    </g>
    <g class="pillar">
      <rect class="frame" x="829" y="222" width="112" height="18"/>
      <rect class="frame" x="844" y="246" width="82" height="11"/>
      <rect class="frame" x="861" y="264" width="48" height="11"/>
      <rect class="frame" x="861.5" y="285" width="47" height="156"/>
      <rect class="frame" x="861" y="447" width="48" height="11"/>
      <rect class="frame" x="844" y="464" width="82" height="12"/>
      <rect class="frame" x="830" y="482" width="110" height="18"/>
      <text class="pillar-label" font-size="18" transform="translate(884,363) rotate(-90)">STRATEGIC</text>
      <text class="pillar-label" font-size="18" transform="translate(902,363) rotate(-90)">ALLIANCES</text>
    </g>

    <!-- foundation -->
    <g class="foundation">
      <rect class="frame" x="273" y="508" width="669" height="100"/>
      <polygon class="tab" points="477,508 723,508 705,536 495,536"/>
      <text class="tab-label" x="600" y="527">FIDUCIARY RESPONSIBILITES</text>
      <text class="duty-line" x="608" y="561">ACCURATE FINANCIALS / INTERNAL CONTROLS / BRAND PROTECTION</text>
      <text class="duty-line" x="609" y="579">/ COMPLIANCE / ETHICS / COST MANAGEMENT</text>
    </g>
  </svg>
</main>
</body>
</html>
```